Business Card for a Dental Office

The design should communicate integrity, quality and reliability. We also want the card look elegant, simple, but still stand out, different from the traditional-dental-office business card.

Industry/Entity Type

Business

```html
<!DOCTYPE html>
<html lang="en">
<head>
<meta charset="UTF-8">
<title>Harlow Dental Centre – Business Card</title>
<link rel="stylesheet" href="https://fonts.googleapis.com/css2?family=Lato:wght@400;700;900&display=swap">
<style>
  :root {
    --canvas-bg: #ececec;
    --card-white: #ffffff;
    --yellow-light: #f3ea1f;
    --yellow-deep: #d6b719;
    --ink: #111111;
    --gold: #c49a12;
    --shadow: rgba(0, 0, 0, 0.18);
  }
  * { margin: 0; padding: 0; box-sizing: border-box; }
  html, body {
    width: 1200px;
    height: 900px;
    overflow: hidden;
    background: var(--canvas-bg);
    font-family: "Lato", Arial, sans-serif;
    color: var(--ink);
  }
  .canvas { position: relative; width: 1200px; height: 900px; }

  .card {
    position: absolute;
    box-shadow: 0 6px 18px var(--shadow);
    overflow: hidden;
  }

  /* Front card */
  .card-front {
    left: 238px; top: 62px;
    width: 555px; height: 343px;
    background: linear-gradient(180deg, var(--yellow-light) 0%, var(--yellow-deep) 100%);
  }
  .person { position: absolute; left: 40px; top: 36px; }
  .person-name { font-size: 21px; font-weight: 700; line-height: 1.2; }
  .person-role { font-size: 15px; font-weight: 400; margin-top: 3px; }

  .address {
    position: absolute; left: 40px; top: 146px;
    font-size: 15px; line-height: 19px; font-style: normal;
  }
  .contact-list {
    position: absolute; left: 44px; top: 198px;
    list-style: none; font-size: 14.5px;
  }
  .contact-list li {
    display: flex; align-items: center; gap: 10px;
    height: 20px;
  }
  .contact-list svg { width: 10px; height: 10px; fill: var(--ink); flex: none; }

  .brand-front {
    position: absolute; left: 300px; top: 70px;
    width: 230px;
    display: flex; flex-direction: column; align-items: center; gap: 16px;
  }
  .brand-square {
    width: 120px; height: 120px;
    background: var(--ink);
  }
  .brand-name-front {
    font-size: 20px; font-weight: 900;
    text-transform: uppercase; letter-spacing: 1px;
    text-align: center; line-height: 1.2;
    color: var(--ink);
  }

  /* Back card */
  .card-back {
    left: 457px; top: 518px;
    width: 560px; height: 344px;
    background: var(--card-white);
  }
  .brand-back {
    position: absolute; left: 70px; top: 120px;
    display: flex; align-items: center; gap: 16px;
  }
  .brand-back .brand-square {
    width: 90px; height: 90px;
    background: var(--gold);
  }
  .brand-name-back {
    font-size: 31px; font-weight: 900;
    text-transform: uppercase; letter-spacing: 0.5px;
    line-height: 1; color: var(--ink);
  }
  .tagline {
    margin-top: 8px;
    font-size: 14.5px; font-weight: 700;
    text-transform: uppercase; letter-spacing: 1.2px;
    color: var(--gold);
  }
</style>
</head>
<body>
<main class="canvas">

  <section class="card card-front" aria-label="Business card front">
    <div class="person">
      <h1 class="person-name">Daniel Morgan</h1>
      <p class="person-role">Managing Director</p>
    </div>

    <address class="address">
      1234, Address Goes Here<br>
      Country Name, 123456
    </address>

    <ul class="contact-list">
      <li>
        <svg viewBox="0 0 10 10" aria-hidden="true"><path d="M2.5 0h5v10h-5zM3.3 1v7h3.4V1z"/></svg>
        123-456-7890
      </li>
      <li>
        <svg viewBox="0 0 10 10" aria-hidden="true"><path d="M0 3.5C1 1 9 1 10 3.5L8.5 4.5 7 3.5H3L1.5 4.5zM2 5h6l1 4H1z"/></svg>
        123-456-7890
      </li>
      <li>
        <svg viewBox="0 0 10 10" aria-hidden="true"><path d="M3 0h5v3h2v7H0V3h3zM4 1v2h3V1zM2 5v1h2V5zm3 0v1h2V5zM2 7v1h2V7zm3 0v1h2V7z"/></svg>
        123-456-7890
      </li>
      <li>
        <svg viewBox="0 0 10 10" aria-hidden="true"><path d="M0 2h10v6H0zM0.8 2.6 5 5.6l4.2-3z" fill-rule="evenodd"/></svg>
        info@youremail.com
      </li>
      <li>
        <svg viewBox="0 0 10 10" aria-hidden="true"><path d="M4 6 6 4M3.5 4.5 2 6a1.4 1.4 0 0 0 2 2l1.5-1.5M6.5 5.5 8 4a1.4 1.4 0 0 0-2-2L4.5 3.5" stroke="#111" stroke-width="1.2" fill="none"/></svg>
        www.yourweb.com
      </li>
    </ul>

    <div class="brand-front">
      <div class="brand-square"></div>
      <p class="brand-name-front">Harlow Dental Centre</p>
    </div>
  </section>

  <section class="card card-back" aria-label="Business card back">
    <div class="brand-back">
      <div class="brand-square"></div>
      <div>
        <p class="brand-name-back">Harlow Dental Centre</p>
        <p class="tagline">Your smile is your gift to others</p>
      </div>
    </div>
  </section>

</main>
</body>
</html>
```